New Business Card Design Project LORVANTI-Italy

we are LORVANTI-Italy
our company in the market for 3 years we are luxury cosmetic company and its about time for a facelift :)
i will like to have elegant luxurious and unique business card
that will give the person that get it a unique, luxurious and elegant impression
I'm VERY OPEN FOR NEW IDEAS , even duo i add a few files of things that i see on line and i like them

i add my logo as well
my website is LORVANTI.COM
(if you would like to see the main style that we have)

Target Market(s)

adult that have money :)

Industry/Entity Type

Business

Contact Information for Business Card

Name - Dario Lorvanti
Position - CEO and CO Founder
address - 4817 E Halvern
telephone - 555-384-1926
email - dario@lorvanti.com
fax - 555-384-1926
website - LORVANTI.COM

Colors
000000
959595
fbee3e
ffffff

Requirements
Must have
• big logo in GOLD color
• elegant look
• impressive
Nice to have
• not must but maybe classy pattern background
• not must but maybe emblem
• maybe clear plastic business card
Should not have
• colors
• images

```html
<!DOCTYPE html>
<html lang="en">
<head>
<meta charset="utf-8">
<title>LORVANTI Italy – Business Card</title>
<link href="https://fonts.googleapis.com/css2?family=Cinzel:wght@400;700&family=Source+Sans+3:wght@400&display=swap" rel="stylesheet">
<style>
  :root {
    --backdrop: #d0d0d0;
    --card-gold: #c9a536;
    --card-gold-light: #d8b94a;
    --card-black: #131313;
    --foil: #d4ad45;
    --white: #ffffff;
  }
  html, body {
    margin: 0;
    padding: 0;
    width: 1200px;
    height: 900px;
    overflow: hidden;
    background: var(--backdrop);
  }
  .stage {
    position: relative;
    width: 1200px;
    height: 900px;
  }
  .card {
    position: absolute;
    top: 271px;
    width: 458px;
    height: 282px;
    border-radius: 14px;
    overflow: hidden;
  }
  .card-front {
    left: 137px;
    background: var(--card-gold);
    color: var(--white);
  }
  .card-back {
    left: 626px;
    background: var(--card-black);
  }
  .emblem-area {
    position: absolute;
    left: 238px;
    top: -10px;
    width: 300px;
    height: 300px;
    border-radius: 50%;
    background: radial-gradient(circle, var(--card-gold-light) 0%, rgba(216,185,74,0.55) 55%, rgba(201,165,54,0) 72%);
  }
  .holder-name {
    position: absolute;
    left: 35px;
    top: 52px;
    margin: 0;
    font-family: "Cinzel", serif;
    font-weight: 700;
    font-size: 22px;
    letter-spacing: 0.3px;
    text-transform: uppercase;
  }
  .holder-title {
    position: absolute;
    left: 35px;
    top: 81px;
    margin: 0;
    font-family: "Source Sans 3", sans-serif;
    font-size: 13.5px;
  }
  .contact-list {
    position: absolute;
    left: 35px;
    top: 117px;
    margin: 0;
    padding: 0;
    list-style: none;
    font-family: "Source Sans 3", sans-serif;
    font-size: 14px;
  }
  .contact-list li {
    display: flex;
    align-items: center;
    height: 22.5px;
  }
  .contact-list svg {
    width: 16px;
    height: 16px;
    margin-right: 6px;
    flex: none;
  }
  .address {
    position: absolute;
    left: 35px;
    top: 217px;
    margin: 0;
    font-family: "Source Sans 3", sans-serif;
    font-size: 14px;
  }
  .brand-circle {
    position: absolute;
    left: 180px;
    top: 42px;
    width: 94px;
    height: 94px;
    border: 3px solid var(--foil);
    border-radius: 50%;
  }
  .brand-name {
    position: absolute;
    left: 0;
    width: 458px;
    top: 158px;
    margin: 0;
    text-align: center;
    font-family: "Cinzel", serif;
    font-weight: 400;
    font-size: 42px;
    line-height: 1;
    color: var(--foil);
    letter-spacing: 0.5px;
  }
  .brand-rule {
    position: absolute;
    left: 118px;
    top: 213px;
    width: 222px;
    height: 2px;
    background: var(--foil);
  }
  .brand-origin {
    position: absolute;
    left: 0;
    width: 458px;
    top: 221px;
    margin: 0;
    text-align: center;
    font-family: "Cinzel", serif;
    font-weight: 400;
    font-size: 17px;
    color: var(--foil);
    letter-spacing: 1px;
  }
</style>
</head>
<body>
<main class="stage">

  <section class="card card-front" aria-label="Business card front">
    <div class="emblem-area" role="img" aria-label="Faint emblem pattern area"></div>
    <h1 class="holder-name">Dario Lorvanti</h1>
    <p class="holder-title">CEO and CO Founder</p>
    <ul class="contact-list">
      <li>
        <svg viewBox="0 0 16 16" aria-hidden="true"><circle cx="8" cy="8" r="8" fill="#fff"/><path d="M4.2 6.6c0-1.4 1.7-2.3 3.8-2.3s3.8.9 3.8 2.3l-1.4.4-.4-1.1c-.6-.2-1.3-.3-2-.3s-1.4.1-2 .3l-.4 1.1zM5.2 7.4h5.6l.8 3.8H4.4z" fill="#c9a536"/></svg>
        555-384-1926
      </li>
      <li>
        <svg viewBox="0 0 16 16" aria-hidden="true"><circle cx="8" cy="8" r="8" fill="#fff"/><rect x="5.5" y="3.8" width="5" height="3" fill="#c9a536"/><rect x="4.2" y="6.5" width="7.6" height="4.2" rx="0.8" fill="#c9a536"/><rect x="5.5" y="9.5" width="5" height="2.8" fill="#c9a536"/></svg>
        555-384-1926
      </li>
      <li>
        <svg viewBox="0 0 16 16" aria-hidden="true"><circle cx="8" cy="8" r="8" fill="#fff"/><rect x="4" y="5" width="8" height="6" rx="0.6" fill="#c9a536"/><path d="M4.3 5.4 8 8.4l3.7-3" stroke="#fff" stroke-width="0.9" fill="none"/></svg>
        dario@lorvanti.com
      </li>
      <li>
        <svg viewBox="0 0 16 16" aria-hidden="true"><circle cx="8" cy="8" r="8" fill="#fff"/><circle cx="8" cy="8" r="4" fill="none" stroke="#c9a536" stroke-width="1.2"/><path d="M4 8h8M8 4c-1.6 2.4-1.6 5.6 0 8M8 4c1.6 2.4 1.6 5.6 0 8" stroke="#c9a536" stroke-width="0.9" fill="none"/></svg>
        WWW.LORVANTI.COM
      </li>
    </ul>
    <p class="address">4817 E Halvern</p>
  </section>

  <section class="card card-back" aria-label="Business card back">
    <div class="brand-circle" aria-hidden="true"></div>
    <p class="brand-name">LORVANTI</p>
    <div class="brand-rule" aria-hidden="true"></div>
    <p class="brand-origin">ITALY</p>
  </section>

</main>
</body>
</html>
```